Naturopath Practitioner Card Design

I am a naturopath needing a design for a business card mainly to show that I am a naturopath and have some contact details to give to prospective clients. I am open minded about the design and what is on the second side of the card whether it just be some artwork or space for details, appointment times etc. Naturopathy is the practice of natural medicine that uses a holistic approach and incorporates herbal and nutritional medicine.

Industry/Entity Type

Business

Contact Information for Business Card

Tom Rudd NaturopathBHSc (Naturopathy) Member WHPG 0487 925 316 tom.rudd@mailexample.com www.tomruddnaturopathy.example.au

Requirements
Nice to have
• Would prefer some kind of original pattern/art work/logo rather than an image, not fussed if its very simple/basic
• I am open to any colour but think I would prefer a more earthy sandy clay etc type style than the greens that are commonly associated with naturopathy.
Should not have
• Don't really want to have generic stock images on it

```html
<!DOCTYPE html>
<html lang="en">
<head>
<meta charset="utf-8">
<title>Tom Rudd Naturopath – Business Card</title>
<link rel="stylesheet" href="https://fonts.googleapis.com/css2?family=Source+Sans+3:wght@400;600;700&display=swap">
<style>
  :root {
    --stage: #2e2e2e;
    --card: #ffffff;
    --green: #2fa52a;
    --green-bright: #a8d92a;
    --green-soft: #dcebc4;
    --ink: #1c1c1c;
    --rule: #333333;
  }
  * { box-sizing: border-box; margin: 0; padding: 0; }
  html, body {
    width: 1200px; height: 900px; overflow: hidden;
    background: var(--stage);
    font-family: "Source Sans 3", sans-serif;
  }
  .stage {
    position: relative; width: 1200px; height: 900px;
    display: flex; align-items: center; justify-content: center; gap: 50px;
  }
  .card {
    position: relative; width: 530px; height: 324px;
    background: var(--card); border-radius: 22px; overflow: hidden;
  }

  /* Front */
  .card-front__photo {
    position: absolute; inset: 0;
    background:
      radial-gradient(ellipse 55% 70% at 28% 62%, var(--green-bright) 0%, rgba(168,217,42,0.55) 35%, rgba(220,235,196,0) 75%),
      linear-gradient(100deg, #c8e39a 0%, var(--green-soft) 30%, #f3f8ec 55%, var(--card) 72%);
  }
  .card-front__details {
    position: absolute; right: 30px; top: 86px;
    text-align: right; color: var(--ink);
    font-size: 15px; line-height: 1.3;
  }
  .card-front__name {
    color: var(--green); font-size: 22px; font-weight: 600; line-height: 1.2;
  }
  .card-front__contact { margin-top: 22px; }
  .contact-line { display: flex; justify-content: flex-end; align-items: center; gap: 6px; }
  .contact-line svg { width: 13px; height: 13px; fill: var(--green); }

  /* Back */
  .card-back__heading {
    position: absolute; top: 34px; left: 0; right: 0; text-align: center;
    color: var(--green); font-size: 21px; font-weight: 700;
  }
  .card-back__form {
    position: absolute; top: 92px; left: 38px; right: 38px;
    color: var(--ink); font-size: 15px; font-weight: 700;
  }
  .form-row { display: flex; align-items: flex-end; gap: 6px; margin-bottom: 22px; }
  .form-row .fill { flex: 1; border-bottom: 2px dotted var(--rule); height: 1px; margin-bottom: 4px; }
  .form-row .fill--short { flex: 0 0 130px; }
  .form-row .spacer { flex: 1; }
  .card-back__notice {
    position: absolute; top: 200px; left: 38px; right: 20px;
    color: var(--green); font-size: 14.5px; font-weight: 700;
  }
  .card-back__grass {
    position: absolute; left: 0; right: 0; bottom: 0; height: 110px;
    background: linear-gradient(180deg, rgba(47,165,42,0) 0%, rgba(47,165,42,0.35) 55%, rgba(47,165,42,0.6) 100%);
  }
</style>
</head>
<body>
<main class="stage">
  <section class="card card-front" aria-label="Business card front">
    <div class="card-front__photo" role="img" aria-label="Soft-focus photograph of a fresh green leaf sprouting"></div>
    <div class="card-front__details">
      <p class="card-front__name">Tom Rudd</p>
      <p>Naturopath</p>
      <p>BHSc (Naturopathy) Member WHPG</p>
      <div class="card-front__contact">
        <p class="contact-line">0487 925 316
          <svg viewBox="0 0 24 24" aria-hidden="true"><path d="M6.6 10.8a15.1 15.1 0 0 0 6.6 6.6l2.2-2.2c.3-.3.7-.4 1-.2 1.1.4 2.3.6 3.6.6.6 0 1 .4 1 1V20c0 .6-.4 1-1 1C10.6 21 3 13.4 3 4c0-.6.4-1 1-1h3.5c.6 0 1 .4 1 1 0 1.3.2 2.5.6 3.6.1.3 0 .7-.2 1z"/></svg>
        </p>
        <p class="contact-line">tom.rudd@mailexample.com
          <svg viewBox="0 0 24 24" aria-hidden="true"><path d="M2 5h20v14H2z M2 5l10 8 10-8" stroke="#fff" stroke-width="1.5"/></svg>
        </p>
      </div>
    </div>
  </section>

  <section class="card card-back" aria-label="Business card back">
    <h2 class="card-back__heading">Your Next Appointment on</h2>
    <div class="card-back__form">
      <div class="form-row"><span class="spacer"></span><span class="fill" style="flex:0 0 300px"></span><span class="spacer"></span></div>
      <div class="form-row">Name :<span class="fill"></span>Time :<span class="fill fill--short"></span>AM / PM</div>
      <div class="form-row">Date :<span class="fill" style="flex:0 0 150px"></span><span class="spacer"></span></div>
    </div>
    <p class="card-back__notice">If unable to keep appointment, kindly give 24hrs notice.</p>
    <div class="card-back__grass" role="img" aria-label="Illustration of green grass blades along the bottom edge"></div>
  </section>
</main>
</body>
</html>
```